Basic business card

use my newly created logo - and the phrases (Lower Cost of Test & Accelarated New Product Introduction) - and my new email domain / ID - use at conferences / tradeshows

Industry/Entity Type

semiconductor

Contact Information for Business Card

Daniel K Forde, Owner, communicate via Logo - Lower COT - Cost of Test, Accelerated NPI - New Product Introduction, phone +1 555 613 0946, Chandler, Arizona, USA, daniel.forde@qal-vub.com

Font styles to use
Sans Serif

Requirements
Nice to have
• re-use my logo created via Pixel Harbor last August (#7315926)

```html
<!DOCTYPE html>
<html lang="en">
<head>
<meta charset="utf-8">
<title>QAL-VUB Business Card</title>
<link rel="stylesheet" href="https://fonts.googleapis.com/css2?family=Open+Sans:wght@400;600&family=Montserrat:wght@700&display=swap">
<style>
  :root {
    --stage: #232323;
    --card: #1f1f22;
    --pattern: #29292d;
    --green: #7bc143;
    --orange: #f5961f;
    --slate: #4b5470;
    --white: #ffffff;
    --text-font: "Open Sans", Arial, sans-serif;
    --name-font: "Montserrat", Arial, sans-serif;
  }
  * { box-sizing: border-box; margin: 0; padding: 0; }
  html, body { width: 1200px; height: 780px; overflow: hidden; background: var(--stage); }
  .canvas { position: relative; width: 1200px; height: 780px; }
  .card {
    position: absolute; width: 620px; height: 354px;
    background: var(--card); border-radius: 22px;
    border: 4px solid var(--green); overflow: hidden;
  }
  .card-back { left: 60px; top: 30px; }
  .card-front { left: 520px; top: 396px; }

  .back-pattern {
    position: absolute; inset: 0; background: var(--pattern);
  }
  .back-wordmark {
    position: absolute; right: 40px; bottom: 44px;
    font-family: var(--text-font); font-weight: 400; font-size: 30px;
    letter-spacing: 2px; color: var(--slate);
  }

  .front-wordmark {
    position: absolute; left: 40px; top: 140px;
    font-family: var(--text-font); font-weight: 400; font-size: 50px;
    letter-spacing: 3px; color: var(--slate);
  }
  .divider {
    position: absolute; left: 316px; top: 44px; width: 2px; height: 186px;
    background: var(--white);
  }
  .details {
    position: absolute; left: 340px; top: 40px; color: var(--white);
    font-family: var(--text-font);
  }
  .name { font-family: var(--name-font); font-weight: 700; font-size: 23px; line-height: 1; }
  .name .first { color: var(--green); }
  .name .last { color: var(--orange); }
  .title { font-size: 12.5px; font-weight: 600; margin: 5px 0 0 18px; }
  .address { font-size: 12px; line-height: 1.35; margin: 16px 0 0 30px; }
  .contact-list { list-style: none; margin: 14px 0 0 30px; font-size: 12px; line-height: 1.55; }
  .contact-list li { display: flex; align-items: center; gap: 8px; }
  .contact-list svg { width: 12px; height: 12px; flex: none; }
  .bands { position: absolute; left: 0; bottom: 0; width: 612px; height: 110px; }
</style>
</head>
<body>
<main class="canvas">

  <section class="card card-back" aria-label="Card back">
    <div class="back-pattern" role="img" aria-label="Embossed repeating pattern of the company symbol"></div>
    <div class="back-wordmark">QAL-VUB</div>
  </section>

  <section class="card card-front" aria-label="Card front">
    <div class="front-wordmark">QAL-VUB</div>
    <div class="divider"></div>

    <div class="details">
      <h1 class="name"><span class="first">Helena</span> <span class="last">Varga</span></h1>
      <p class="title">Managing Director</p>
      <p class="address">4180 Linden Ave. Suite<br>310 Mesa Ridge, TX 75900</p>
      <ul class="contact-list">
        <li>
          <svg viewBox="0 0 12 12" aria-hidden="true"><path fill="#7bc143" d="M2.4 1l2 2-1 1.3a7 7 0 0 0 4.3 4.3L9 7.6l2 2-1.4 1.4C5.5 11 1 6.5 1 2.4z"/></svg>
          (555) 420-8813
        </li>
        <li>
          <svg viewBox="0 0 12 12" aria-hidden="true"><rect x="1" y="2.5" width="10" height="7" rx="1" fill="#7bc143"/><path d="M1.5 3l4.5 3.5L10.5 3" fill="none" stroke="#1f1f22" stroke-width="1"/></svg>
          info@qal-vub.com
        </li>
        <li>
          <svg viewBox="0 0 12 12" aria-hidden="true"><circle cx="6" cy="6" r="5" fill="#7bc143"/><path d="M1 6h10M6 1c-2 2.5-2 7.5 0 10M6 1c2 2.5 2 7.5 0 10" fill="none" stroke="#1f1f22" stroke-width="0.8"/></svg>
          www.qal-vub.com
        </li>
      </ul>
    </div>

    <svg class="bands" viewBox="0 0 612 110" aria-hidden="true">
      <path fill="var(--orange)" d="M300 54 L612 24 L612 46 L330 72 Q316 73 300 54 Z"/>
      <path fill="var(--green)" d="M0 92 L290 66 Q310 64 322 78 L0 108 Z"/>
    </svg>
  </section>

</main>
</body>
</html>
```